Business card for denture clinic Veltrimora

We need a new business card with our new logo. We are a denture clinic in New Zealand with our target market being 45+ years old. We would need a space on the back to write our patients next appointment on. We would space for only one appointment rather than a list. We will attach a photo showing an example of this. But of course, we would like to see your twist on this. We want it to be bold and easy to read and a good mixture of professional but modern. We have attached our logo to be used on the card.

Target Market(s)

People aged 45+ needing dentures

Industry/Entity Type

Dental

Contact Information for Business Card

We want our logo on the front and the space to write an appointment on the back. I've attached an example our our old business card showing this. We need to have the technicians details on the front.

Font styles to use
Sans Serif

Colors
0255a3
919191
fbfbfb

Requirements
Must have
• The following details:
• Liam Dorsett BDT, PGDipCDentTech Calverin
• Dental Prosthetist
• Phone numbers: 0800 47 3125
• 09 572 1394
• Email: liam@veltrimora.co.nz
• www.veltrimora.co.nz
• Address: 14 Marlow Crest Road
• Halbrook West
• Auckland 0793
Nice to have
• We would like our business cards to have more than just two colours as we want them to be more vibrant. We have uploaded an example of a business card we liked that showed this.

```html
<!DOCTYPE html>
<html lang="en">
<head>
<meta charset="utf-8">
<title>Veltrimora Business Card</title>
<link rel="stylesheet" href="https://fonts.googleapis.com/css2?family=Open+Sans:wght@300;400;600;700&family=Titillium+Web:wght@300;400&display=swap">
<style>
  :root {
    --brand-blue: #0255a3;
    --brand-blue-light: #1a74c6;
    --brand-grey: #919191;
    --paper: #fbfbfb;
    --ink: #4a4a4a;
    --backdrop: #e8eaed;
  }
  * { box-sizing: border-box; margin: 0; padding: 0; }
  html, body { width: 1200px; height: 950px; overflow: hidden; }
  body {
    background: var(--backdrop);
    font-family: "Open Sans", Arial, sans-serif;
    position: relative;
  }
  .card {
    position: absolute;
    left: 230px;
    width: 740px;
    height: 420px;
    border-radius: 26px;
    overflow: hidden;
    box-shadow: 0 10px 28px rgba(0,0,0,0.18);
  }
  .card-front { top: 45px; background: var(--paper); }
  .card-back { top: 495px; background: var(--brand-blue); }
  .card-art { position: absolute; inset: 0; }

  .technician {
    position: absolute; top: 26px; right: 40px;
    text-align: right; color: #fff;
  }
  .technician-name { font-weight: 700; font-size: 26px; letter-spacing: 0.5px; }
  .technician-quals { font-weight: 600; font-size: 19px; margin-top: 2px; }
  .technician-role { font-weight: 300; font-size: 18px; margin-top: 2px; }

  .address {
    position: absolute; top: 252px; right: 40px;
    text-align: right; color: var(--ink);
    font-size: 18px; line-height: 1.45; font-style: normal;
  }

  .brand { position: absolute; left: 40px; top: 150px; }
  .brand-lockup { display: flex; align-items: center; gap: 12px; }
  .brand-square {
    width: 46px; height: 46px; border-radius: 6px;
    background: var(--brand-blue-light);
  }
  .brand-name {
    font-family: "Titillium Web", Arial, sans-serif;
    font-weight: 400; font-size: 40px; letter-spacing: 1px;
    color: var(--brand-blue-light); line-height: 1;
  }
  .brand-tagline {
    margin: 4px 0 0 58px;
    font-size: 11px; letter-spacing: 3.5px;
    color: var(--brand-grey);
  }

  .contacts {
    position: absolute; left: 40px; top: 238px;
    list-style: none; color: var(--ink); font-size: 16px;
  }
  .contacts li { display: flex; align-items: center; gap: 10px; height: 24px; }
  .contact-icon { width: 16px; height: 16px; flex: none; }

  .appointment-title {
    position: absolute; left: 50px; top: 70px;
    color: #fff; font-weight: 700; font-size: 34px; letter-spacing: 2px;
  }
  .back-mark {
    position: absolute; right: 70px; top: 50px;
    width: 180px; height: 180px; border-radius: 10px;
    background: #fff;
  }
  .appointment-strip {
    position: absolute; left: 0; right: 0; top: 280px; height: 72px;
    background: #fff; display: flex; align-items: center;
    color: var(--brand-blue); font-size: 18px;
  }
  .strip-cell-lead { width: 130px; height: 100%; border-right: 2px solid var(--brand-blue); }
  .strip-time { flex: 1; padding-left: 18px; }
  .strip-ampm { padding-right: 40px; }
</style>
</head>
<body>

<section class="card card-front" aria-label="Business card front">
  <svg class="card-art" viewBox="0 0 740 420" aria-hidden="true">
    <path d="M200 0 C270 60 330 160 420 192 C510 222 620 230 740 234 V215 C620 212 520 200 440 175 C360 150 300 60 230 0Z" fill="var(--brand-grey)" opacity="0.75"/>
    <path d="M230 0 H740 V215 C620 212 520 200 440 175 C360 150 300 60 230 0Z" fill="var(--brand-blue)"/>
    <path d="M0 318 C70 326 140 366 200 420 H180 C130 376 70 345 0 338Z" fill="var(--brand-grey)" opacity="0.75"/>
    <path d="M0 338 C70 345 130 376 180 420 H0Z" fill="var(--brand-blue)"/>
  </svg>

  <div class="technician">
    <p class="technician-name">LIAM DORSETT BDT</p>
    <p class="technician-quals">PGDipCDentTech Calverin</p>
    <p class="technician-role">Dental Prosthetist</p>
  </div>

  <address class="address">
    14 Marlow Crest Road<br>
    Halbrook West<br>
    Auckland 0793
  </address>

  <div class="brand">
    <div class="brand-lockup">
      <span class="brand-square"></span>
      <span class="brand-name">VELTRIMORA</span>
    </div>
    <p class="brand-tagline">THE DENTURE EXPERTS</p>
  </div>

  <ul class="contacts">
    <li>
      <svg class="contact-icon" viewBox="0 0 16 16"><path d="M4 1 L6.5 4.5 L5 6 C6 8 8 10 10 11 L11.5 9.5 L15 12 L13 15 C7 14 2 9 1 3Z" fill="var(--brand-blue)"/></svg>
      0800 47 3125
    </li>
    <li>
      <svg class="contact-icon" viewBox="0 0 16 16"><rect x="1" y="3" width="14" height="11" rx="2" fill="var(--brand-blue)"/><rect x="4" y="1" width="8" height="4" rx="1" fill="var(--brand-blue)"/><circle cx="8" cy="9.5" r="2.5" fill="#fff"/></svg>
      09 572 1394
    </li>
    <li>
      <svg class="contact-icon" viewBox="0 0 16 16"><rect x="1" y="3" width="14" height="10" rx="1.5" fill="var(--brand-blue)"/><path d="M2 4 L8 9 L14 4" stroke="#fff" stroke-width="1.4" fill="none"/></svg>
      liam@veltrimora.co.nz
    </li>
    <li>
      <svg class="contact-icon" viewBox="0 0 16 16"><circle cx="8" cy="8" r="7" fill="var(--brand-blue)"/><ellipse cx="8" cy="8" rx="3" ry="7" stroke="#fff" stroke-width="1" fill="none"/><path d="M1 8 H15" stroke="#fff" stroke-width="1"/></svg>
      www.veltrimora.co.nz
    </li>
  </ul>
</section>

<section class="card card-back" aria-label="Business card back">
  <h2 class="appointment-title">NEXT APPOINTMENT</h2>
  <div class="back-mark"></div>
  <div class="appointment-strip">
    <span class="strip-cell-lead"></span>
    <span class="strip-time">Time:</span>
    <span class="strip-ampm">AM/PM</span>
  </div>
</section>

</body>
</html>
```